Business card for Eyelash extension salon in Beverly Hills,California USA

We need new business card for our salon in Beverly Hills. The salon name is 'Lashvera' . We would like to have...Business name: Lashvera Name of person: will provide later Address 4720 N.Alder Crest Ave Beverly Hills , CA 90210 Phone: will provide later (Text only) Web: www.lashverastudio.example Snapgrid icon, Circlebook icon follow us for seasonal campaign and news @lashverastudiolounge Design should look elegant, high-end, clean, simple, cohesive with my brand. Please refer my brand board. Business name color will be metallic bronzy color. Im thinking grey background or white background. Thanks

Target Market(s)

25-35. Gender neutral. People who are in Entertainment business industry.
This is High-end Eyelash extension salon in Beverly Hills

Industry/Entity Type

Beauty Salon

Contact Information for Business Card

Business name: Lashvera
Name of person: will provide later
Address 4720 N.Alder Crest Ave Beverly Hills , CA 90210
Phone: will provide later (Text only)
Web: www.lashverastudio.example
Snapgrid icon, Circlebook icon
follow us for seasonal campaign and news @lashverastudiolounge

Requirements
Must have
• Beautiful, elegant, clean and simple look but very attractive and modern
Should not have
• We don't like too clutter, too busy designs.

```html
<!DOCTYPE html>
<html lang="en">
<head>
<meta charset="utf-8">
<title>Lashvera – Business Card</title>
<link rel="stylesheet" href="https://fonts.googleapis.com/css2?family=Cormorant+Garamond:wght@500;600&family=DM+Serif+Display&display=swap">
<style>
  :root {
    --backdrop: #bfe4d8;
    --card: #ffffff;
    --bronze: #8c5a3a;
    --marble-deep: rgba(150, 150, 155, 0.42);
    --marble-soft: rgba(190, 190, 195, 0.18);
    --card-shadow: rgba(40, 90, 75, 0.22);
  }
  * { box-sizing: border-box; margin: 0; padding: 0; }
  html, body {
    width: 1200px;
    height: 856px;
    overflow: hidden;
  }
  body {
    position: relative;
    background: var(--backdrop);
    font-family: "Cormorant Garamond", Georgia, serif;
    color: var(--bronze);
  }
  .card {
    position: absolute;
    width: 540px;
    height: 309px;
    background: var(--card);
    border-radius: 28px;
    box-shadow: 0 14px 30px var(--card-shadow);
    overflow: hidden;
  }
  .card--front { left: 600px; top: 90px; }
  .card--back  { left: 110px; top: 450px; }

  .card__marble {
    position: absolute;
    inset: 0;
    background:
      radial-gradient(ellipse 140px 60px at 8% 100%, var(--marble-deep), transparent 70%),
      radial-gradient(ellipse 120px 50px at 92% 0%, var(--marble-deep), transparent 70%),
      radial-gradient(ellipse 60px 120px at 0% 55%, var(--marble-soft), transparent 70%),
      radial-gradient(ellipse 60px 120px at 100% 45%, var(--marble-soft), transparent 70%),
      radial-gradient(ellipse 110px 40px at 70% 100%, var(--marble-soft), transparent 70%),
      radial-gradient(ellipse 110px 40px at 30% 0%, var(--marble-soft), transparent 70%);
  }

  .brand {
    position: absolute;
    inset: 0;
    display: flex;
    align-items: center;
    justify-content: center;
  }
  .brand__name {
    font-family: "Cormorant Garamond", Georgia, serif;
    font-weight: 500;
    font-size: 64px;
    letter-spacing: 4px;
    color: var(--bronze);
  }

  .contact {
    position: absolute;
    inset: 0;
    display: flex;
    flex-direction: column;
    align-items: center;
    justify-content: center;
    text-align: center;
    padding-top: 4px;
  }
  .contact__name {
    font-family: "DM Serif Display", Georgia, serif;
    font-size: 30px;
    line-height: 1;
    letter-spacing: 0.5px;
  }
  .contact__role {
    font-size: 15px;
    font-weight: 500;
    margin-bottom: 12px;
  }
  .contact__line {
    font-size: 16px;
    font-weight: 600;
    line-height: 1.2;
  }
  .contact__label { font-weight: 600; }
  .social {
    display: flex;
    gap: 14px;
    margin-top: 10px;
    font-size: 14px;
    font-weight: 600;
  }
  .social__item {
    display: inline-flex;
    align-items: center;
    gap: 5px;
  }
  .social__dot {
    width: 9px;
    height: 9px;
    border: 1.4px solid var(--bronze);
    border-radius: 2px;
  }
  .contact__handle {
    font-size: 16px;
    font-weight: 600;
    margin-top: 2px;
  }
  .contact__web {
    font-size: 17px;
    font-weight: 600;
    letter-spacing: 1.6px;
    margin-top: 12px;
  }
</style>
</head>
<body>

  <section class="card card--front" aria-label="Card front">
    <div class="card__marble" role="img" aria-label="Soft grey marble texture along the card edges"></div>
    <div class="brand">
      <span class="brand__name">Lashvera</span>
    </div>
  </section>

  <section class="card card--back" aria-label="Card back">
    <div class="card__marble" role="img" aria-label="Soft grey marble texture along the card edges"></div>
    <div class="contact">
      <h1 class="contact__name">Rowan Ellery</h1>
      <p class="contact__role">Owner</p>
      <p class="contact__line"><span class="contact__label">P:</span> +1 555 014 2287 | <span class="contact__label">E:</span> hello@lashverastudio.example</p>
      <p class="contact__line">4720 N.Alder Crest Ave Beverly Hills</p>
      <p class="contact__line">CA 90210</p>
      <div class="social">
        <span class="social__item"><span class="social__dot"></span>Circlebook</span>
        <span class="social__item"><span class="social__dot"></span>Snapgrid</span>
      </div>
      <p class="contact__handle">@lashverastudiolounge</p>
      <p class="contact__web">www.lashverastudio.example</p>
    </div>
  </section>

</body>
</html>
```